Cool business cards

Use my existing logo from mark meadow (see images I have uploaded) and design a really cool non-stuffy business card. I am a divorce mediator.

```html
<!DOCTYPE html>
<html lang="en">
<head>
<meta charset="utf-8">
<title>Mark Meadow, J.D. — Business Cards</title>
<link rel="stylesheet" href="https://fonts.googleapis.com/css2?family=Montserrat:wght@600;700&family=Questrial&display=swap">
<style>
  :root {
    --backdrop: #3b3f41;
    --card: #ffffff;
    --brand-blue: #0a66b0;
    --brand-orange: #f5821f;
    --ink-gray: #9a9a9a;
    --tag-gray: #7c7c7c;
  }
  * { box-sizing: border-box; margin: 0; padding: 0; }
  html, body { width: 1200px; height: 1000px; overflow: hidden; }
  body { background: var(--backdrop); position: relative; font-family: "Questrial", sans-serif; }

  .card {
    position: absolute;
    background: var(--card);
  }
  .card--front { left: 126px; top: 89px; width: 702px; height: 384px; }
  .card--back  { left: 382px; top: 529px; width: 714px; height: 389px; }

  /* front */
  .front-mark {
    position: absolute; left: 0; right: 0; top: 172px;
    display: flex; align-items: center; justify-content: center; gap: 14px;
  }
  .front-mark__dot {
    width: 34px; height: 34px; border-radius: 50%; background: var(--brand-orange);
  }
  .front-mark__name {
    font-family: "Montserrat", sans-serif; font-weight: 700;
    font-size: 30px; letter-spacing: 1px; color: var(--brand-blue);
  }

  /* back: identity block */
  .identity {
    position: absolute; left: 44px; top: 124px; width: 260px;
    display: flex; flex-direction: column; align-items: center;
  }
  .identity__dot {
    width: 100px; height: 100px; border-radius: 50%; background: var(--brand-blue);
  }
  .identity__name {
    margin-top: 16px;
    font-family: "Montserrat", sans-serif; font-weight: 700;
    font-size: 22px; letter-spacing: 0.5px; color: var(--brand-blue); white-space: nowrap;
  }
  .identity__tagline {
    margin-top: 2px;
    display: flex; align-items: center; gap: 6px;
    font-family: "Montserrat", sans-serif; font-weight: 600;
    font-size: 9.5px; letter-spacing: 0.6px; color: var(--tag-gray); white-space: nowrap;
  }
  .identity__tagline::before,
  .identity__tagline::after {
    content: ""; width: 20px; height: 1px; background: var(--tag-gray);
  }

  /* back: contact block */
  .holder-name {
    position: absolute; left: 376px; top: 50px;
    font-family: "Montserrat", sans-serif; font-weight: 700;
    font-size: 21px; letter-spacing: 0.5px; color: var(--ink-gray);
  }
  .contacts { position: absolute; left: 370px; top: 210px; list-style: none; }
  .contacts__item {
    display: flex; align-items: center; gap: 11px;
    height: 42.5px; font-size: 22px; color: var(--ink-gray);
  }
  .contacts__icon { width: 26px; height: 26px; flex: none; fill: var(--ink-gray); }
</style>
</head>
<body>

<section class="card card--front" aria-label="Card front">
  <div class="front-mark">
    <span class="front-mark__dot"></span>
    <span class="front-mark__name">MARK MEADOW</span>
  </div>
</section>

<section class="card card--back" aria-label="Card back">
  <div class="identity">
    <span class="identity__dot"></span>
    <p class="identity__name">MARK MEADOW, J.D.</p>
    <p class="identity__tagline">DIVORCE &amp; FAMILY MEDIATION</p>
  </div>

  <p class="holder-name">NAME</p>

  <ul class="contacts">
    <li class="contacts__item">
      <svg class="contacts__icon" viewBox="0 0 24 24" aria-hidden="true">
        <path d="M6.6 10.8a15.1 15.1 0 0 0 6.6 6.6l2.2-2.2c.3-.3.7-.4 1-.2 1.1.4 2.3.6 3.6.6.6 0 1 .4 1 1V20c0 .6-.4 1-1 1A17 17 0 0 1 3 4c0-.6.4-1 1-1h3.5c.6 0 1 .4 1 1 0 1.3.2 2.5.6 3.6.1.3 0 .7-.2 1z"/>
      </svg>
      <span>+00 000000000</span>
    </li>
    <li class="contacts__item">
      <svg class="contacts__icon" viewBox="0 0 24 24" aria-hidden="true">
        <path d="M2 5h20v14H2z M3.5 6.5 12 13l8.5-6.5" fill="none" stroke="#9a9a9a" stroke-width="0"/>
        <path d="M2 5h20v14H2zm1.8 1.5L12 12.6l8.2-6.1zM3.5 8v9.5h17V8L12 14.4z"/>
      </svg>
      <span>name@markmeadow.com</span>
    </li>
    <li class="contacts__item">
      <svg class="contacts__icon" viewBox="0 0 24 24" aria-hidden="true" fill="none" stroke="#9a9a9a" stroke-width="1.6">
        <circle cx="12" cy="12" r="10"/>
        <ellipse cx="12" cy="12" rx="4.2" ry="10"/>
        <path d="M2 12h20M4 7h16M4 17h16"/>
      </svg>
      <span>www.markmeadow.com</span>
    </li>
  </ul>
</section>

</body>
</html>
```